Classy, Elegant, Simple Business Card Design

Looking to have a classy, simple, and elegant design. Want a top notch designed business card. I really like the look of the new torvane credit card. I also like the design I attached. I am trying to reach 21-29 year old females for booking us for there wedding or event. We offer Disc Jockey Service, Photo Booth Rentals, and Uplighting .

Target Market(s)

21-28 year old females

Contact Information for Business Card

Has to have logo, website, email, and phone number

Font styles to use
Other font styles liked:
• open to font choice, modern, clean
Designer to choose
33a6d7
0791cd
0555a3
ffffff

Requirements
Must have
• Has to have logo, website, email, and phone number
Nice to have
• I really like the design of the new torvane credit card. I also included my logo and some designs I like
Should not have
• clutter or too much info

```html
<!DOCTYPE html>
<html lang="en">
<head>
<meta charset="utf-8">
<title>Tidecrest Event Group – Business Card</title>
<link href="https://fonts.googleapis.com/css2?family=Open+Sans:wght@400;600;700&display=swap" rel="stylesheet">
<style>
  :root {
    --backdrop: #3a3a3c;
    --card: #29292b;
    --card-edge: #1f1f21;
    --silver: #8d8d91;
    --blue-light: #33a6d7;
    --blue: #0791cd;
    --blue-deep: #0555a3;
    --white: #ffffff;
    --muted: #d9d9dc;
    --divider: #55555a;
  }
  * { box-sizing: border-box; margin: 0; padding: 0; }
  html, body {
    width: 799px;
    height: 1200px;
    overflow: hidden;
    background: var(--backdrop);
    font-family: "Open Sans", Arial, sans-serif;
  }
  .sheet {
    width: 799px;
    height: 1200px;
    display: flex;
    flex-direction: column;
    justify-content: space-around;
    align-items: center;
    padding: 60px 0;
  }
  .card {
    position: relative;
    width: 640px;
    height: 366px;
    background: var(--card);
    border: 1px solid var(--card-edge);
    box-shadow: 0 10px 30px rgba(0,0,0,0.45);
    overflow: hidden;
  }

  /* Front */
  .card-front {
    display: flex;
    align-items: center;
    justify-content: center;
  }
  .brand-front {
    display: flex;
    align-items: center;
    gap: 16px;
    color: var(--silver);
    font-weight: 600;
    font-size: 40px;
    letter-spacing: 2px;
  }
  .brand-front .brand-dot {
    width: 22px;
    height: 22px;
    border-radius: 50%;
    background: var(--silver);
  }
  .brand-front .brand-name { line-height: 1.15; text-align: left; }
  .brand-front .brand-name span { display: block; }

  /* Back */
  .card-back .brand-back {
    position: absolute;
    left: 40px;
    top: 118px;
    width: 250px;
    color: var(--blue);
    font-weight: 600;
    font-size: 27px;
    letter-spacing: 1px;
    line-height: 1.2;
  }
  .card-back .brand-back span { display: block; }
  .card-back .divider {
    position: absolute;
    left: 312px;
    top: 40px;
    height: 220px;
    border-left: 2px dotted var(--divider);
  }
  .person {
    position: absolute;
    left: 350px;
    top: 92px;
  }
  .person-name {
    color: var(--blue);
    font-weight: 700;
    font-size: 26px;
    line-height: 1.1;
  }
  .person-role {
    color: var(--white);
    font-size: 14px;
    margin-top: 2px;
  }
  .contact-list {
    list-style: none;
    margin-top: 22px;
  }
  .contact-list li {
    display: flex;
    align-items: center;
    gap: 10px;
    color: var(--white);
    font-size: 15px;
    line-height: 24px;
  }
  .contact-list svg { width: 14px; height: 14px; flex: none; }
  .service-band {
    position: absolute;
    right: 0;
    bottom: 0;
    width: 400px;
    height: 48px;
    border-top-left-radius: 26px;
    background: linear-gradient(90deg, var(--blue-deep), var(--blue));
    color: var(--white);
    font-size: 15px;
    display: flex;
    align-items: center;
    padding-left: 40px;
    letter-spacing: 0.3px;
  }
</style>
</head>
<body>
<main class="sheet">

  <section class="card card-front" aria-label="Card front">
    <div class="brand-front">
      <div class="brand-dot"></div>
      <div class="brand-name"><span>TIDECREST</span><span>EVENT GROUP</span></div>
    </div>
  </section>

  <section class="card card-back" aria-label="Card back">
    <div class="brand-back"><span>TIDECREST</span><span>EVENT GROUP</span></div>
    <div class="divider"></div>

    <div class="person">
      <p class="person-name">Evan Marlow</p>
      <p class="person-role">Founder &amp; CEO</p>
      <ul class="contact-list">
        <li>
          <svg viewBox="0 0 16 16" aria-hidden="true"><path fill="#0791cd" d="M3 1.5l2.5-.5 1.5 3.5-1.8 1.2a9 9 0 0 0 5.1 5.1l1.2-1.8 3.5 1.5-.5 2.5c-.2.6-.8 1-1.5 1C6.6 14.5 1.5 9.4 1.5 3c0-.7.4-1.3 1.5-1.5z"/></svg>
          952 5550 1486
        </li>
        <li>
          <svg viewBox="0 0 16 16" aria-hidden="true"><rect x="1" y="3" width="14" height="10" fill="#0791cd"/><path d="M1 3l7 6 7-6" fill="none" stroke="#29292b" stroke-width="1.4"/></svg>
          evan@tidecrest.com
        </li>
        <li>
          <svg viewBox="0 0 16 16" aria-hidden="true"><circle cx="8" cy="8" r="6.5" fill="none" stroke="#0791cd" stroke-width="1.6"/><path d="M1.5 8h13M8 1.5c-3 3.5-3 9.5 0 13M8 1.5c3 3.5 3 9.5 0 13" fill="none" stroke="#0791cd" stroke-width="1.2"/></svg>
          www.tidecrest.com
        </li>
      </ul>
    </div>

    <div class="service-band">Disc Jockeys | Photo Booths | And More</div>
  </section>

</main>
</body>
</html>
```